Garlic Farm for Farm Sales/Restaurant sales

Need a professional, but appealing to agriculture world. We are selling 27 kinds of Organic Garlic from a farm in Simla,CO. I have uploaded logo and business information-we are going to need a template, because I will need to use it for four separate people.
-We are trying to appeal to Farm to table restaurants
-As well as growers/farmers

Target Market(s)

Agriculture Sales/Restaurants-Organic

Industry/Entity Type

Agriculture

Contact Information for Business Card

Want it to look more unique then your average kelto stock card- I want it to look amazing

Font styles to use
Sans Serif

Colors
0455a3
ec1f27
fbed22
ffffff

Requirements
Must have
• Just be creative
Nice to have
• Colorful
Should not have
• plain

```html
<!DOCTYPE html>
<html lang="en">
<head>
<meta charset="utf-8">
<title>Ridgeline Garlic – Business Card</title>
<link rel="stylesheet" href="https://fonts.googleapis.com/css2?family=Source+Sans+3:wght@400;600;700&display=swap">
<style>
  :root {
    --backdrop: #8e8e8e;
    --card-white: #f7f7f7;
    --card-grey: #ececec;
    --band-red: #a81e3a;
    --stripe-red: #d2504a;
    --brand-navy: #1d3263;
    --brand-red: #c8202c;
    --text-white: #ffffff;
    --text-yellow: #f6d21a;
  }
  * { box-sizing: border-box; margin: 0; padding: 0; }
  html, body { width: 1200px; height: 900px; overflow: hidden; }
  body {
    background: var(--backdrop);
    font-family: "Source Sans 3", "Myriad Pro", sans-serif;
    display: flex;
    flex-direction: column;
    align-items: center;
    justify-content: center;
    gap: 24px;
  }
  .card {
    width: 700px;
    height: 400px;
    position: relative;
    overflow: hidden;
    box-shadow: 0 6px 18px rgba(0,0,0,0.25);
  }
  .brand {
    display: flex;
    align-items: center;
    gap: 14px;
  }
  .brand-dot {
    width: 54px; height: 54px;
    border-radius: 50%;
    background: var(--brand-red);
  }
  .brand-name {
    color: var(--brand-navy);
    font-weight: 700;
    font-size: 40px;
    letter-spacing: 0.5px;
    line-height: 1;
  }

  /* Front */
  .card-front { background: var(--card-white); }
  .card-front .brand {
    position: absolute;
    top: 120px; left: 0; right: 0;
    justify-content: center;
  }
  .front-band {
    position: absolute;
    left: 0; right: 0; bottom: 0;
    height: 132px;
    background: var(--band-red);
    display: flex;
    align-items: center;
    justify-content: center;
  }
  .website {
    color: var(--text-white);
    font-size: 22px;
    font-weight: 600;
    letter-spacing: 0.5px;
  }

  /* Back */
  .card-back { background: var(--card-grey); }
  .card-back .brand {
    position: absolute;
    top: 70px; right: 44px;
  }
  .back-stripe {
    position: absolute;
    left: 0; right: 0;
    top: 198px;
    height: 5px;
    background: var(--stripe-red);
  }
  .back-band {
    position: absolute;
    left: 0; right: 0; bottom: 0;
    top: 210px;
    background: var(--band-red);
    padding: 22px 40px 0;
    color: var(--text-yellow);
  }
  .person {
    display: flex;
    align-items: baseline;
    gap: 12px;
    margin-bottom: 12px;
  }
  .person-name {
    color: var(--text-white);
    font-weight: 700;
    font-size: 30px;
  }
  .person-role { font-size: 27px; font-weight: 400; }
  .contact-line { font-size: 20px; line-height: 1.45; }
  .contact-line .sep { margin: 0 6px; }
</style>
</head>
<body>
  <section class="card card-front">
    <div class="brand">
      <span class="brand-dot"></span>
      <span class="brand-name">ridgeline garlic</span>
    </div>
    <div class="front-band">
      <span class="website">www.ridgelinegarlic.com</span>
    </div>
  </section>

  <section class="card card-back">
    <div class="brand">
      <span class="brand-dot"></span>
      <span class="brand-name">ridgeline garlic</span>
    </div>
    <div class="back-stripe"></div>
    <div class="back-band">
      <div class="person">
        <span class="person-name">Dana Reyes</span>
        <span class="person-role">| Owner</span>
      </div>
      <p class="contact-line">P: 555-014-2270<span class="sep">|</span>F: (555)-014-2270<span class="sep">|</span>E: hello@ridgelinegarlic.com</p>
      <p class="contact-line">PO Box 1182, Lakeview, CO 80999</p>
    </div>
  </section>
</body>
</html>
```